Brochure for people who suffer from Sleep Apnea and need a medical device called a CPAP Machine

I want a brochure that can be placed in doctors offices with my competitors brochures. It needs to be bold and stand out and deliver a very strong message that draws the patients away from our competitors and to us. I have included a word document generally outlining some of my requirements and thoughts, please review prior to investing time into design!

Target Market(s)

people who suffer from sleep apnea, which is a disease that causes them to stop breathing many times per hour, resulting in the patient needing to wear a device called a CPAP Machine. This is an illness that can impact anyone but is more likely to impact those suffering from obesity and men.

Industry/Entity Type

Health Care

Other font styles liked:
• Use what you think is best

Colors

Designer to choose colors to be used in the design.

Requirements
Must have
• Please see word document for must have items, and feel free to contact me with any questions.
• Also must have bold colors, and/or graphics to really stand out among my competitors brochures.
Nice to have
• Would prefer to use the baby picture titled "sleeping baby 4" if possible but provided 2 other baby photos just in case. Whatever you want to add, use your professional creativity! You Don't need to use all the pictures uploaded!!!!!
Should not have
• Nothing discriminatory or offensive.

```html
<!DOCTYPE html>
<html lang="en">
<head>
<meta charset="utf-8">
<title>RestWell Direct – Sleep Apnea Brochure</title>
<link href="https://fonts.googleapis.com/css2?family=Open+Sans:wght@400;600&family=Nunito:wght@800;900&display=swap" rel="stylesheet">
<style>
:root{
  --green:#2fb36a;
  --green-soft:#6cc592;
  --purple:#8a4fa6;
  --purple-deep:#5e3a73;
  --paper:#f3f2f4;
  --ink:#2b2b2b;
}
*{box-sizing:border-box;margin:0;padding:0}
html,body{width:1200px;height:1200px;overflow:hidden;background:#fff}
body{font-family:"Open Sans",Arial,sans-serif;color:var(--ink);position:relative}
.spread{position:absolute;left:185px;width:830px;height:580px;background:var(--paper);overflow:hidden}
.spread--outside{top:10px}
.spread--inside{top:610px}
.abs{position:absolute}

/* outside: panel 1 */
.intro-panel{left:15px;top:15px;width:252px;height:552px;background:var(--green-soft);color:#fff;
  padding:18px 14px;font-size:11px;line-height:1.58;text-align:justify}
.intro-panel p{margin-bottom:13px}
.intro-panel p.tight{margin-bottom:0}

/* outside: panel 2 */
.problem-panel{left:285px;top:22px;width:260px}
.lead-line{font-size:15.5px;color:var(--purple-deep)}
.sub-head{font-family:"Nunito",sans-serif;font-weight:900;color:var(--green);font-size:18px;margin:14px 0 0 4px}
.big-head{left:290px;top:118px;font-family:"Nunito",sans-serif;font-weight:900;color:var(--green);font-size:26px;line-height:1.2;width:110px}
.photo-mask{left:396px;top:86px;width:150px;height:186px;background:linear-gradient(160deg,#5a5a5a,#1d1d1d 60%,#8d8d90)}
.guarantee{left:290px;top:290px;width:260px;font-size:13.5px;line-height:1.35;color:#3a3a3a}
.faint-name{left:290px;top:350px;font-size:34px;color:#d7ebdf;white-space:nowrap}
.seal{left:376px;top:338px;width:80px;height:80px;border-radius:50%;background:radial-gradient(circle,#f6c744 0 58%,#c9302c 60% 100%)}
.cta{left:290px;top:428px;width:252px;background:var(--purple);color:#fff;font-size:17.5px;line-height:1.25;padding:6px 20px}
.address{left:293px;top:486px;font-size:10.5px;line-height:17px;color:#333}
.address .web b{color:var(--purple);font-weight:400}
.address .web i{color:var(--green);font-style:normal}

/* outside: panel 3 (cover) */
.brand{display:flex;align-items:center;gap:8px;white-space:nowrap}
.brand-dot{width:18px;height:18px;border-radius:50%;background:var(--green)}
.brand-name{color:var(--purple);font-weight:400}
.cover-brand{left:565px;top:68px}
.cover-brand .brand-name{font-size:31px}
.tagline{left:568px;top:128px;width:258px;text-align:center;font-family:"Nunito",sans-serif;font-weight:800;font-size:16px}
.baby-photo{left:562px;top:162px;width:258px;height:108px;background:linear-gradient(90deg,#c9d4e6,#f3e9e3 50%,#e8d7cc)}
.how-badge{left:575px;top:170px;width:96px;height:96px;border-radius:50%;background:var(--purple-deep);color:#fff;
  display:flex;flex-direction:column;align-items:center;justify-content:center;font-size:15.5px;line-height:1.2;text-align:center}
.how-badge b{font-family:"Nunito",sans-serif;font-weight:900;font-size:19px}
.different{left:563px;top:276px;white-space:nowrap;color:var(--purple);font-size:15px}
.different b{font-family:"Nunito",sans-serif;font-weight:900;color:var(--green);font-size:26px}
.everything{left:563px;top:312px;width:258px;text-align:center;letter-spacing:6px;font-weight:600;font-size:17px;color:#444}
.perks{left:575px;top:344px;list-style:none;font-size:10.5px;line-height:1.7;color:#333}
.perks li::before{content:"";display:inline-block;width:6px;height:6px;border-radius:50%;background:var(--green);margin-right:8px;vertical-align:1px}
.store-head{color:var(--purple-deep);font-size:20px;font-weight:400;white-space:nowrap}
.cover-store{left:563px;top:456px}
.contact{list-style:none}
.contact li{display:flex;align-items:center;gap:12px;color:#333;height:26px}
.contact svg{flex:none}
.cover-contact{left:563px;top:490px;font-size:15px}

/* inside spread */
.bed-photo{left:0;top:0;width:830px;height:580px;background:linear-gradient(115deg,#f4f3f3 0%,#e6e2de 35%,#efeae6 55%,#d9d5d2 80%,#ecebec 100%);opacity:.9}
.story{left:48px;top:14px;width:740px;font-size:11.3px;line-height:1.72;color:#333}
.story p{margin-bottom:9px}
.story .gap{margin-top:16px}
.help-flag{left:287px;top:36px;background:var(--green);color:#fff;font-family:"Nunito",sans-serif;font-weight:900;font-size:24px;padding:0 6px;line-height:32px}
.inside-brand{left:0;width:830px;justify-content:center;top:372px}
.inside-brand .brand-dot{width:24px;height:24px}
.inside-brand .brand-name{font-size:50px}
.inside-store{left:34px;top:458px}
.inside-contact{left:34px;top:492px;font-size:15px}
.delivery-badge{left:690px;top:460px;width:100px;height:100px;border-radius:50%;background:radial-gradient(circle,#d63a30 0 48%,#7a7a7a 50% 100%)}
</style>
</head>
<body>

<section class="spread spread--outside">
  <div class="abs intro-panel">
    <p>Anyone can give you CPAP Supplies. However we are committed to providing you with exceptional customer service too.</p>
    <p>How do we do this? By giving you services no other CPAP retailer offers, like…</p>
    <p class="tight">…Free Home Visits: We bring the store to you so we can give you as much time you need and set up all you equipment and supplies for you.</p>
    <p class="tight">…Free Delivery: So you never need to come to the store (Unless you want to!).</p>
    <p class="tight">… Night and Weekend Appointments: Because not everyone works 9-to-5.</p>
    <p class="tight">…A Dedicated Clinician: Because we also want to be your friend.</p>
    <p class="tight">… Hardship and Financial-assistance Programs: To make sure everyone gets the care they need.</p>
    <p>… Promise of Guaranteed Success: We offer 30-day guarantees on all supplies so you know you are getting the best care possible.</p>
    <p>Why are YOU Settling for LESS?<br>Let US treat you RIGHT!</p>
    <p>We Make CPAP Personal!</p>
  </div>

  <div class="abs problem-panel">
    <p class="lead-line">CPAP Doesn’t need to be like this!</p>
    <p class="sub-head">Let us make sure</p>
  </div>
  <h2 class="abs big-head">This doesn’t happen to you</h2>
  <div class="abs photo-mask" role="img" aria-label="Photo of a wide-eyed man wearing a full CPAP mask and hose"></div>
  <p class="abs guarantee">We Guarantee Your CPAP Success,<br>because your Success is our reputation.</p>
  <div class="abs faint-name">RestWell Direct</div>
  <div class="abs seal" role="img" aria-label="Satisfaction guarantee seal"></div>
  <div class="abs cta">Call for an Appointment<br>(Or just to talk) Today</div>
  <div class="abs address">
    555-014-2267<br>48 Maple Row<br>Brookhaven, Ontario L0X 1A0<br>Serving all of Ontario<br>
    <span class="web">www.<i>RestWell</i><b>Direct</b>.com</span>
  </div>

  <div class="abs brand cover-brand"><span class="brand-dot"></span><span class="brand-name">RestWell Direct</span></div>
  <p class="abs tagline">Want Sleep Like A Baby Again?</p>
  <div class="abs baby-photo" role="img" aria-label="Photo of a smiling newborn baby sleeping on a white blanket"></div>
  <div class="abs how-badge">Let us<br>show You<b>How!</b></div>
  <p class="abs different">What Makes us <b>Different?</b></p>
  <p class="abs everything">EVERYTHING!</p>
  <ul class="abs perks">
    <li>Free Home Visits</li>
    <li>Free delivery</li>
    <li>Night and weekend appointments</li>
    <li>Specializes exclusively in Sleep Therapy</li>
    <li>A dedicated clinician assigned directly to you</li>
    <li>Hardship and financial-assistance programs</li>
  </ul>
  <h3 class="abs store-head cover-store">We Bring The Store To You</h3>
  <ul class="abs contact cover-contact">
    <li><svg width="20" height="20" viewBox="0 0 20 20"><rect width="20" height="20" rx="2" fill="#2f7d52"/><path d="M6 4l2.5 2.5-1.3 1.8c.9 1.8 2 2.9 3.8 3.8l1.8-1.3L15.3 13.3 13.5 15.5C8.5 15 5 11.5 4.5 6.5z" fill="#fff"/></svg>555-014-2267</li>
    <li><svg width="20" height="20" viewBox="0 0 20 20"><rect width="20" height="20" rx="2" fill="#2fb36a"/><path d="M10 3.5a4.2 4.2 0 0 0-4.2 4.2c0 3.2 4.2 8 4.2 8s4.2-4.8 4.2-8A4.2 4.2 0 0 0 10 3.5z" fill="#fff"/><circle cx="10" cy="7.7" r="1.6" fill="#2fb36a"/></svg>Serving all of Ontario</li>
    <li><svg width="20" height="20" viewBox="0 0 20 20"><rect width="20" height="20" rx="2" fill="#6cc592"/><circle cx="10" cy="10" r="5.5" fill="none" stroke="#fff" stroke-width="1.4"/><path d="M4.5 10h11M10 4.5c-2.4 3-2.4 8 0 11M10 4.5c2.4 3 2.4 8 0 11" fill="none" stroke="#fff" stroke-width="1"/></svg>www.RestWellDirect.com</li>
  </ul>
</section>

<section class="spread spread--inside">
  <div class="abs bed-photo" role="img" aria-label="Soft faded photo of a couple sleeping peacefully in a white bed"></div>

  <div class="abs story">
    <p>When you get diagnosed with Obstructive Sleep Apnea it can be overwhelming.</p>
    <p class="gap" style="margin-bottom:0">We will:</p>
    <p style="margin-bottom:0">•Visit you in the comfort of your own home so we can privately discuss Sleep Apnea, explain what to expect next, and answer any and all your questions in a relaxed, comfortable environment.&nbsp; You don’t get this from any other CPAP Retailer.</p>
    <p style="margin-bottom:0">•Figure out the best equipment and supplies you need to guarantee your success… We will even set up everything for before we leave so you know it is set up right!</p>
    <p>•We are committed to your success.&nbsp; We will spend as much time with you as necessary to make sure all your questions are answered and every concern is addressed.</p>
    <p class="gap">There are many resources available for you on our website at www.RestWellDirect.com.<br>We Love To Talk. You don’t have to be a customer to call us, we will answer any questions you have!<br>Check out our 5-Star reviews on ReviewHub (By Searching for RestWell Direct)!</p>
  </div>
  <h2 class="abs help-flag">We are here to help.</h2>

  <div class="abs brand inside-brand"><span class="brand-dot"></span><span class="brand-name">RestWell Direct</span></div>

  <h3 class="abs store-head inside-store">We Bring The Store To You</h3>
  <ul class="abs contact inside-contact">
    <li><svg width="20" height="20" viewBox="0 0 20 20"><rect width="20" height="20" rx="2" fill="#2f7d52"/><path d="M6 4l2.5 2.5-1.3 1.8c.9 1.8 2 2.9 3.8 3.8l1.8-1.3L15.3 13.3 13.5 15.5C8.5 15 5 11.5 4.5 6.5z" fill="#fff"/></svg>555-014-2267</li>
    <li><svg width="20" height="20" viewBox="0 0 20 20"><rect width="20" height="20" rx="2" fill="#2fb36a"/><path d="M10 3.5a4.2 4.2 0 0 0-4.2 4.2c0 3.2 4.2 8 4.2 8s4.2-4.8 4.2-8A4.2 4.2 0 0 0 10 3.5z" fill="#fff"/><circle cx="10" cy="7.7" r="1.6" fill="#2fb36a"/></svg>Serving all of Ontario</li>
    <li><svg width="20" height="20" viewBox="0 0 20 20"><rect width="20" height="20" rx="2" fill="#6cc592"/><circle cx="10" cy="10" r="5.5" fill="none" stroke="#fff" stroke-width="1.4"/><path d="M4.5 10h11M10 4.5c-2.4 3-2.4 8 0 11M10 4.5c2.4 3 2.4 8 0 11" fill="none" stroke="#fff" stroke-width="1"/></svg>www.RestWellDirect.com</li>
  </ul>
  <div class="abs delivery-badge" role="img" aria-label="Free delivery badge"></div>
</section>

</body>
</html>
```